Brochure for a website accessibility report

This brochure is related to a report that www.qelvantrix.org sell. The report shows the results of an automated audit of a websites accessibility. It shows details of issues found with screen shots, examples of code and provides remediation advice.

The brochure will be a pdf 8.5 inches by 11 inches. It can be anywhere from 6 to 10 pages.

The FlintVue™ name itself should be “Bree Serif” font. The fonts, styles, colors and sizes are up to you.

The images used and logo of the Office of Digital Reachworks and K7P logo are upload

We highlighted in blue page extracts from the report we sell. Do not use the blue highlight, it is merely there to show you where the specific examples of the report we sell are vs the other content in the report. The areas in blue which show the content from the actual report should be shown as an extract of the actual page of the report. You have flexibility to change the layout and the way the content look.

The red square callouts over the blue content are callouts that describe the specific page extracts. We used it as a red callout only so that you would be able to see it. You should change the specific location, look and feel of the callout to be appropriate

Target Market(s)

Marketing and Technical people

Industry/Entity Type

Information Technology

Font styles to use
Sans Serif

Colors

Designer to choose colors to be used in the design.

Requirements
Should not have
• wheelchairs, images of blind people

```html
<!DOCTYPE html>
<html lang="en">
<head>
<meta charset="utf-8">
<title>FlintVue™ Brochure 2019 – Section 1</title>
<link href="https://fonts.googleapis.com/css2?family=Bree+Serif&family=Montserrat:wght@300;400;500;600;700;800&display=swap" rel="stylesheet">
<style>
  :root {
    --green: #25b06e;
    --orange: #f7ac1c;
    --ink: #111111;
    --rule: #d9d9d9;
    --paper: #ffffff;
  }
  * { margin: 0; padding: 0; box-sizing: border-box; }
  html, body { width: 972px; height: 1200px; overflow: hidden; background: var(--paper); }
  body { position: relative; font-family: "Montserrat", Arial, sans-serif; color: var(--ink); }

  .side-band { position: absolute; left: 0; top: 0; }

  .masthead { position: absolute; left: 261px; top: 60px; }
  .masthead__product { font-family: "Bree Serif", Georgia, serif; font-size: 16px; line-height: 18px; }
  .masthead__edition { font-family: "Bree Serif", Georgia, serif; font-size: 16px; line-height: 18px; color: var(--green); }
  .masthead-rule { position: absolute; left: 261px; top: 113px; width: 434px; height: 2px; background: #eeeeee; }

  .publisher { position: absolute; right: 67px; top: 70px; display: flex; align-items: center; gap: 8px; }
  .publisher__mark { width: 12px; height: 12px; border-radius: 50%; background: var(--green); }
  .publisher__name { font-size: 13px; font-weight: 600; line-height: 16px; color: var(--ink); white-space: nowrap; }

  .section-head { position: absolute; left: 261px; top: 178px; width: 644px; display: flex; align-items: center; }
  .section-head__toggle { width: 28px; height: 29px; background: var(--orange); display: flex; align-items: center; justify-content: center; }
  .section-head__title { font-size: 38px; font-weight: 700; margin-left: 17px; letter-spacing: -0.5px; line-height: 38px; }
  .section-head__rule { flex: 1; height: 1.5px; background: var(--orange); margin-left: 20px; margin-top: 2px; }

  .intro { position: absolute; left: 261px; top: 232px; width: 648px; font-size: 17.5px; font-weight: 300; line-height: 24px; }

  .chart-title { position: absolute; left: 261px; top: 315px; }
  .chart-title__kicker { font-size: 32px; font-weight: 700; color: var(--green); line-height: 40px; }
  .chart-title__main { font-size: 30px; font-weight: 800; line-height: 36px; }
  .chart-title__bar { position: absolute; left: 261px; top: 406px; width: 266px; height: 8px; background: var(--green); }

  .chart-note { position: absolute; left: 582px; top: 363px; width: 323px; font-size: 14.5px; line-height: 18.5px; text-align: justify; hyphens: auto; }

  .summary { position: absolute; left: 261px; top: 457px; width: 644px; border-collapse: collapse; table-layout: fixed; }
  .summary th { background: var(--green); color: #fff; font-size: 14.5px; font-weight: 700; text-align: left; height: 47px; padding-left: 10px; border-left: 2px solid #fff; }
  .summary th:first-child { border-left: 0; }
  .summary td { height: 47px; font-size: 13px; vertical-align: middle; border-bottom: 1px solid var(--rule); }
  .summary .principle { background: var(--green); color: #fff; font-size: 18.5px; padding-left: 10px; border-bottom: 2px solid #fff; border-right: 2px solid #fff; }
  .summary .guideline { padding-left: 8px; border-right: 1px solid var(--rule); }
  .summary .issues { padding-left: 7px; }
  .summary tr.group-end td:not(.principle) { border-bottom: 2px solid var(--green); }
  .summary tr.last td { border-bottom: 2px solid var(--green); }
  .codes { display: grid; grid-template-columns: repeat(4, 57px); row-gap: 2px; line-height: 15px; }

  .closing { position: absolute; left: 261px; top: 1040px; width: 648px; font-size: 15.5px; font-weight: 700; line-height: 21px; }

  .footer { position: absolute; left: 261px; top: 1142px; width: 644px; display: flex; align-items: center; }
  .footer__url { font-size: 14px; font-weight: 600; }
  .footer__rule { flex: 1; height: 1px; background: var(--green); margin: 0 14px 0 30px; }
  .footer__page { font-size: 13px; color: var(--green); }
</style>
</head>
<body>
  <svg class="side-band" width="170" height="1200" viewBox="0 0 170 1200" aria-hidden="true">
    <polygon points="0,85 169,175 169,1075 0,1167" fill="#25b06e"/>
  </svg>

  <header>
    <div class="masthead">
      <div class="masthead__product">FlintVue™</div>
      <div class="masthead__edition">Brochure 2019</div>
    </div>
    <div class="masthead-rule"></div>
    <div class="publisher">
      <span class="publisher__mark"></span>
      <span class="publisher__name">Office of Digital Reachworks</span>
    </div>
  </header>

  <div class="section-head">
    <span class="section-head__toggle">
      <svg width="12" height="8" viewBox="0 0 12 8" aria-hidden="true"><polyline points="1.5,1.5 6,6 10.5,1.5" fill="none" stroke="#fff" stroke-width="2"/></svg>
    </span>
    <h1 class="section-head__title">Section 1</h1>
    <span class="section-head__rule"></span>
  </div>

  <p class="intro">The first section of the report begins with a Summary Chart that breaks down WCAG 2.1 A/AA issues by principle:</p>

  <h2 class="chart-title">
    <span class="chart-title__kicker">Example WCAG 2.1 A/AA</span><br>
    <span class="chart-title__main">Summary Chart</span>
  </h2>
  <div class="chart-title__bar"></div>

  <p class="chart-note">Checkpoints with failures detected are identified in the “Issues Discovered” col&shy;umn. The detail behind these failures is available in the next section.</p>

  <table class="summary">
    <colgroup><col style="width:168px"><col style="width:263px"><col style="width:213px"></colgroup>
    <thead>
      <tr><th>PRINCIPLE</th><th>GUIDELINE</th><th>ISSUES DISCOVERED</th></tr>
    </thead>
    <tbody>
      <tr><td class="principle" rowspan="4">Perceivable</td><td class="guideline">Guideline 1.1 Text Alternatives</td><td class="issues"><div class="codes"><span>1.1.1</span></div></td></tr>
      <tr><td class="guideline">Guideline 1.2 Time-based Media</td><td class="issues"><div class="codes"><span>1.2.1</span><span>1.2.2</span><span>1.2.3</span><span>1.2.4</span><span>1.2.5</span></div></td></tr>
      <tr><td class="guideline">Guideline 1.3 Adaptable</td><td class="issues"><div class="codes"><span>1.3.1</span><span>1.3.2</span><span>1.3.5</span></div></td></tr>
      <tr class="group-end"><td class="guideline">Guideline 1.4 Distinguishable</td><td class="issues"><div class="codes"><span>1.4.1</span><span>1.4.3</span><span>1.4.4</span><span>1.4.11</span></div></td></tr>
      <tr><td class="principle" rowspan="3">Operable</td><td class="guideline">Guideline 2.1 Keyboard Accessible</td><td class="issues"><div class="codes"><span>2.1.1</span><span>2.1.2</span></div></td></tr>
      <tr><td class="guideline">Guideline 2.2 Enough Time</td><td class="issues"><div class="codes"><span>2.2.1</span><span>2.2.2</span></div></td></tr>
      <tr class="group-end"><td class="guideline">Guideline 2.4 Navigable</td><td class="issues"><div class="codes"><span>2.4.1</span><span>2.4.2</span><span>2.4.4</span><span>2.4.7</span></div></td></tr>
      <tr><td class="principle" rowspan="3">Understandable</td><td class="guideline">Guideline 3.1 Readable</td><td class="issues"><div class="codes"><span>3.1.1</span></div></td></tr>
      <tr><td class="guideline">Guideline 3.2 Predictable</td><td class="issues"></td></tr>
      <tr class="group-end"><td class="guideline">Guideline 3.3 Input Assistance</td><td class="issues"><div class="codes"><span>3.3.2</span></div></td></tr>
      <tr class="last"><td class="principle">Robust</td><td class="guideline">Guideline 4.1 Compatible</td><td class="issues"><div class="codes"><span>4.1.1</span><span>4.1.2</span></div></td></tr>
    </tbody>
  </table>

  <p class="closing">The report then provides full detail about the specific infractions organized by each of the four principles and explains exactly what the problems are.</p>

  <footer class="footer">
    <span class="footer__url">www.qelvantrix.org</span>
    <span class="footer__rule"></span>
    <span class="footer__page">4</span>
  </footer>
</body>
</html>
```